Business cards to launch an education platform

Hi,
I am looking at having new business cards designed.
I am a startup, developing a web platform for schools and university, the education world. It's an online assessment system.
I would like a card that looks classy, and that is using the colors and the font of my logo.

I have attached:
1) my logo
2) A business card that I have designed quickly so you can have all the information required in the card, but I really don't like it.
3) The font that I am using (Lato Regular) to design my web platform
4) Some screenshots of my web platform so you can have a look at the style that I have.

Target Market(s)

Major market: Education system: Schools and university
Minor markets: Business in general

Industry/Entity Type

Business

Contact Information for Business Card

Clara Fenwick
Director

M: 0437 518 902
E: clara.fenwick@amberLoomSystems.com.au

Requirements
Must have
• The colors of my logo

```html
<!DOCTYPE html>
<html lang="en">
<head>
<meta charset="utf-8">
<title>Amber Loom Systems – Business Cards</title>
<link rel="stylesheet" href="https://fonts.googleapis.com/css2?family=Lato:wght@400;700&family=Roboto+Condensed:wght@400;500&family=Roboto:wght@400&display=swap">
<style>
  :root {
    --backdrop: #8f9091;
    --card-stock: #e6e7eb;
    --navy: #04365f;
    --sapphire: #0b4f8a;
    --sky: #2a9bd3;
    --paper-text: #e8edf3;
  }
  * { margin: 0; padding: 0; box-sizing: border-box; }
  html, body {
    width: 1105px;
    height: 1200px;
    overflow: hidden;
    background: var(--backdrop);
  }
  .canvas {
    position: relative;
    width: 1105px;
    height: 1200px;
  }
  .card {
    position: absolute;
    left: 182px;
    width: 746px;
    height: 427px;
    background: var(--card-stock);
    overflow: hidden;
  }
  .card--front { top: 119px; }
  .card--back  { top: 635px; }

  /* Front */
  .front-brand {
    position: absolute;
    top: 0;
    left: 0;
    width: 100%;
    height: 196px;
    display: flex;
    align-items: center;
    justify-content: center;
    gap: 16px;
  }
  .brand-square {
    width: 44px;
    height: 44px;
    background: var(--sapphire);
  }
  .brand-name {
    font-family: "Lato", sans-serif;
    font-weight: 400;
    color: var(--sapphire);
    letter-spacing: 0.06em;
  }
  .front-brand .brand-name { font-size: 30px; }

  .contact-band {
    position: absolute;
    left: 0;
    top: 196px;
    width: 100%;
    height: 231px;
    background: var(--navy);
    text-align: center;
  }
  .holder-name {
    position: absolute;
    top: 70px;
    width: 100%;
    font-family: "Roboto Condensed", sans-serif;
    font-weight: 400;
    font-size: 35px;
    color: var(--sky);
    letter-spacing: 0.01em;
  }
  .holder-title {
    position: absolute;
    top: 115px;
    width: 100%;
    font-family: "Roboto Condensed", sans-serif;
    font-weight: 500;
    font-size: 23px;
    color: var(--paper-text);
  }
  .holder-phone,
  .holder-email {
    position: absolute;
    width: 100%;
    font-family: "Roboto", sans-serif;
    font-size: 20px;
    color: var(--paper-text);
  }
  .holder-phone { top: 153px; }
  .holder-email { top: 181px; }
  .label { color: var(--sky); }

  /* Back */
  .back-brand {
    position: absolute;
    inset: 0;
    display: flex;
    align-items: center;
    justify-content: center;
    gap: 22px;
  }
  .back-brand .brand-square {
    width: 84px;
    height: 84px;
  }
  .back-brand .brand-name { font-size: 40px; }
</style>
</head>
<body>
<main class="canvas">
  <section class="card card--front" aria-label="Business card front">
    <div class="front-brand">
      <span class="brand-square" aria-hidden="true"></span>
      <span class="brand-name">AMBER LOOM SYSTEMS</span>
    </div>
    <div class="contact-band">
      <p class="holder-name">CLARA FENWICK</p>
      <p class="holder-title">DIRECTOR</p>
      <p class="holder-phone"><span class="label">Mobile :</span> 0437 518 902</p>
      <p class="holder-email">clara.fenwick@amberLoomSystems.com.au</p>
    </div>
  </section>

  <section class="card card--back" aria-label="Business card back">
    <div class="back-brand">
      <span class="brand-square" aria-hidden="true"></span>
      <span class="brand-name">AMBER LOOM SYSTEMS</span>
    </div>
  </section>
</main>
</body>
</html>
```